Digital Imaging Website Design Project

This project is for 3 page designs - The main Home page design, department page design & content page design which will utilize most of the home page components.

Client Background - http://www.klmvxco.example

An almost Forty year old established printing company that has a large client base of architect/engineering, as the print shop opened up as a blueprinting company, and over the years has grown, changed and expanded to offer document and digital file management for this industry. KLMVxco. has also always offered color printing services, but recently has expanded their color department to be able to offer amazing dimensional printing, and extreme cutting technology.

These new products and services will be targeted to new industries for repeatable printing needs, promotional, point of purchase color printing, as well as in-store, interior decor/wall. These new printing services are only offered by KLMVXCO in their area, and they want to convey that they are on the leading edge of color printing technology, while at the same time, not eliminating their existing primary business scaring away their traditional client base of architectural/engineering firms that use them for large format printing, scanning and document management services.

1 - Home Page Design
Primary Goals of the design:

1.Provide a new, eye catching engaging website that conveys the above expansion/growth/cutting edge company.
2.Full screen design please to move away from the 'center' bordered up website they currently have.
3.Design Components – We don't have any media to provide you with exception of our logo. We're looking for fresh design that is exciting and engaging imagery. Additionally, we are working on a color/effected version of our logo to place on the color division page, and this will probably tie in with the design you create for us.
4.It should be designed to be able to work as a responsive design as well so that when installed, will work across devices etc..
5.Colors – Same color scheme, but if you have an accent color you'd like to use to make the site pop, go for it!

Requirements:
1.The 4 divisions of the company should be the main feature so that the client depending on which department they are needing, will see those 4 choices clearly in the design, and they'll know to click on one of them to get more information and to their needed services.

2.The main goal of the site is to get visitors to place an order, there should be a feature on the home page for this call to action.

3.Put in an element that communicates the main benefit of KLMVxco. - an area for a 1-line Statement/Call to Action / Overall Company Benefit/

4.The 4 divisions need to have eye catching elements related to their products and services, and that clearly illustrate that the user should click on that to go to the appropriate area for products and services

Reprographics
This department is specifically geared to architect/engineering industry
BYLine for optional Use: Partnering with Building Industry Providers since 1975
Related pages for better understanding:
http://www.klmvxco.example/services/portland_professional_printing_services
http://www.klmvxco.example/services/reprographics
Digital File Management
This department is related to Architect/engineers, but can also apply to any other industry needing electronic document management, scanning, or archival services.
BYLine for optional use: Effective & Efficient Digital Solutions at every level.
Related Pages:
http://www.klmvxco.example/colorgraphics/electronic_file_document_management
http://www.klmvxco.example/colorgraphics/document_scanning_service
http://www.klmvxco.example/services/scanning_and_archiving

Color Graphics
This Department is newly expanded / has expanded services / they are focusing more of their efforts on this department and is a key reason for updated website design.
This Department image/representation should be stellar in the imagery to convey the excellence of the color department the services availble.
One of their newest products/services is dimensional printing – not 3-D, but raised element printing. Essentially a client could pick components on their graphic that that they want to 'bump' out, and additional layers would be put in place to create a popped out, dimensional effect. * Bonus points for creating the color department image that effectively conveys this new service – whether it's showing an abstract image/element that is actually raised off the page/paper/component. Additionally the color dimensional printing can be done on practically any material – glass, vinyl, material etc.... Please let me know if you have any questions on this.
BYLine for optional Use: See How Our Color Stands Out From the Rest
Related pages:
http://www.klmvxco.example/colorgraphics
http://www.klmvxco.example/colorgraphics/color_digital_imaging

Equipment & Supplies
This department provides specific supplies and hardware vs. printing products/services. Our largest client base is architects/engineers, but is not limited to this industry. Typical equipment is large printers, and supplies are typically paper products geared to the large format printing services, for the architect/engineers industry.
Byline for optional Use: In-House Printing & Fulfillment Services
Related pages:
http://www.klmvxco.example/tarvo_ulix_equipment_sales
http://www.klmvxco.example/supplies

Additionally - Possibly have descriptive text sections below these 4 elements, but this is optional.

2.) Department/Division Page design -

This page should pull the home page element to over based on which division is selected.
Have a submenu design incorporated so that users can navigate to all the products and services that will be listed under that division
Contain a plugin design for FAQs – so that depending on which division page they are on, the appropriate FAQ's would display for use to have easy access to.
Contain a plugin design for – Contact Us easy form – short form –
Name
Company
Number
Email
Project Details/Questions: Text box

3.)Content Page design
This page should have main area for content
Area for an image with slideshow of other supporting images
Optional area for video – most (99%) of the pages will not have videos, but in the case we do, would like an area that will display videos effectively.
Optional FAQ plugin display
Contact plugin display

Global Elements:

Static and very visible site features that are in a position so that if user clicks beyond home page will still see these are:
Get a Quote
Place Order
Digital Plan-room
Call Today - 555-384-7290

Other global components:
SM Icons – QN, Chirpa, Workrung
Rotating Testimonial

Navigational Menu:
The HBQ Difference
About
Sustainability
Products & Services
Reprograhics
Digital File Management
Color Graphics
Equipment & Supplies
Login
Blog
Contact Us

After the contest – What would be great to have is when a user clicks on one of the departments, it takes that visual element and continues onto it's department page for a smaller but related image - But this may be an after this web design contest.

Additionally will need some other design work on the interior pages, as well, so hoping to find a great designer to complete the other tasks – as well as be the go-to for future endeavors!

Thanks for looking at the project, and I look forward to any questions you may have.
Updates

Looking forward to hearing from interested designers! - If you're curious about my work, you can find my profile at:  https://www.jobrilly.example/users/~07f3b92e61cd5a0b48

Target Market(s)

Please see description

Industry/Entity Type

Electronic

Requirements
Must have
• Please see description

```html
<!DOCTYPE html>
<html lang="en">
<head>
<meta charset="utf-8">
<title>HBQ Digital Imaging — Harlowe Print &amp; Blueprint</title>
<link rel="stylesheet" href="https://fonts.googleapis.com/css2?family=Signika:wght@400;600&family=Ubuntu:ital,wght@0,400;0,500;1,400&display=swap">
<style>
:root{
  --navy:#0d2d7d;
  --blue:#2f6fd1;
  --menu:#3a78d6;
  --link:#2d74cf;
  --text:#5a5a5a;
  --olive:#6e7c1c;
  --band:#efeee6;
  --footer:#6b771c;
  --line:#dcdcdc;
}
*{box-sizing:border-box;margin:0;padding:0}
html,body{width:960px;height:1200px;overflow:hidden}
body{position:relative;background:#fff;font-family:"Ubuntu",sans-serif;color:var(--text)}
.abs{position:absolute}

/* header */
.site-header{left:0;top:0;width:960px;height:104px;background:#ebebeb;border-bottom:1px solid #d0d0d0}
.brand-mark{left:104px;top:20px;font-family:"Signika",sans-serif;font-weight:600;font-size:56px;line-height:56px;color:var(--navy);letter-spacing:-1px}
.brand-name{left:259px;top:18px;font-family:"Signika",sans-serif;font-weight:600;font-size:16px;line-height:16px;color:var(--navy);text-transform:uppercase}
.brand-tag{left:259px;top:77px;font-family:"Signika",sans-serif;font-style:italic;font-size:11px;color:var(--navy)}
.contact{left:654px;top:27px;font-size:15px;color:#666;line-height:27px}
.contact .phone{font-size:20px;color:var(--link)}
.contact .mail{font-size:13px;color:var(--link)}

/* hero */
.hero{left:0;top:104px;width:960px;height:358px;background:linear-gradient(115deg,#c8442e 0%,#e98a3a 18%,#e7dcae 38%,#4a4a48 55%,#cfa47c 70%,#d8c05a 85%,#7aa0c8 100%)}
.main-nav{left:105px;top:139px;width:176px;background:var(--menu);box-shadow:0 2px 6px rgba(0,0,0,.35);padding:2px 0 4px}
.main-nav li{list-style:none;height:25.6px;line-height:25.6px;font-size:10.5px;color:#fff;padding-left:26px;position:relative;border-bottom:1px dashed rgba(255,255,255,.55)}
.main-nav li:last-child{border-bottom:none}
.main-nav li::before{content:"";position:absolute;left:10px;top:10px;width:6px;height:6px;border-radius:50%;background:rgba(255,255,255,.55)}
.main-nav li.active::before{background:#fff}
.hero-title{right:104px;top:310px;text-align:right;font-family:"Signika",sans-serif;font-weight:600;font-size:35px;line-height:37px;color:#fff;text-shadow:0 2px 4px rgba(0,0,0,.6)}
.slider-dots{left:765px;top:397px;width:91px;height:32px;background:var(--navy);border-radius:3px;display:flex;gap:5px;justify-content:center;align-items:center}
.slider-dots span{width:14px;height:14px;border-radius:3px;background:#6b86c5}
.slider-dots span.on{background:#fff}

/* divisions */
.division-band{left:0;top:515px;width:960px;height:106px;background:var(--band)}
.division{width:176px;height:176px;border-radius:50%;background:#d9d9d9;display:flex;align-items:center;justify-content:center;top:480px}
.division .disc{width:158px;height:158px;border-radius:50%;background:radial-gradient(circle at 50% 30%,#2e72d8 0%,#144aa6 60%,#0a3488 100%);display:flex;align-items:center;justify-content:center;text-align:center;font-family:"Signika",sans-serif;font-weight:600;font-size:26px;line-height:27px;color:#fff;text-shadow:0 1px 2px rgba(0,0,0,.4)}
.division .disc.photo{background:linear-gradient(160deg,#f4f6f9,#c6d0dc 60%,#8ea0b6);color:#111;text-shadow:0 1px 0 rgba(255,255,255,.6);font-size:28px;line-height:29px}

/* about + testimonial */
.section-title{font-size:18px;color:var(--link);font-weight:400}
.about-title{left:105px;top:704px}
.about-text{left:104px;top:732px;width:492px;font-size:10px;line-height:18.5px}
.btn{background:var(--navy);color:#fff;font-size:10px;border-radius:3px;height:22px;line-height:22px;padding:0 10px;text-transform:uppercase}
.about-btn{left:104px;top:802px}
.testi-title{left:616px;top:704px}
.arrows{display:flex;gap:6px}
.arrows span{width:14px;height:14px;border-radius:50%;background:#e4e4e4;box-shadow:0 1px 2px rgba(0,0,0,.3);position:relative}
.arrows span::after{content:"";position:absolute;top:4px;border:3px solid transparent}
.arrows .prev::after{border-right:4px solid #222;left:2px}
.arrows .next::after{border-left:4px solid #222;left:6px}
.testi-arrows{left:820px;top:709px}
.testi-box{left:616px;top:735px;width:240px;height:91px;border:1px solid var(--line);border-radius:3px;background:#fbfbf8;padding:9px 10px;position:absolute}
.testi-quote-mark{position:absolute;left:10px;top:2px;font-family:Georgia,serif;font-size:34px;line-height:34px;color:#c8c8c8}
.testi-box q{display:block;font-style:italic;font-size:9.5px;line-height:16px;quotes:none;text-indent:30px}
.testi-box cite{display:block;text-align:right;font-size:9.5px;color:var(--navy);margin-top:7px}

/* actions */
.divider{left:0;width:960px;height:1px;background:#eaeaea}
.action{top:862px;width:240px;height:62px;background:linear-gradient(#8c9c2a,#667513);border-radius:2px;display:flex;align-items:center;gap:8px;padding-left:28px;font-family:"Signika",sans-serif;font-weight:600;font-size:19px;color:#fff;text-shadow:0 1px 2px rgba(0,0,0,.45);text-transform:uppercase;white-space:nowrap;overflow:hidden}
.action.plan-room{padding-left:8px;gap:6px}

/* news + equipment */
.news-title{left:105px;top:957px}
.news{left:104px;width:305px;font-size:10px}
.news .date{color:var(--navy);font-size:11px;margin-bottom:5px}
.news-1{top:989px;padding-bottom:10px;border-bottom:1px solid var(--line)}
.news-2{top:1037px}
.read-all{left:103px;top:1093px;font-size:10px;color:var(--olive);font-weight:500}
.equip-title{left:447px;top:957px}
.equip-arrows{left:820px;top:962px}
.equip-image{left:448px;top:991px;width:216px;height:124px;border:1px solid var(--line);background:radial-gradient(circle at 50% 55%,#ffffff,#e7e9ec 60%,#d3d6da)}
.equip-name{left:681px;top:988px;font-size:12.5px;color:var(--navy)}
.equip-text{left:681px;top:1005px;width:175px;font-size:9.5px;line-height:16px}
.equip-btn{left:681px;top:1075px}

/* footer */
.site-footer{left:0;top:1128px;width:960px;height:72px;background:var(--footer);color:#e6ebc8;font-size:9px}
.copy{left:104px;top:20px;line-height:21px}
.copy b{color:#fff;font-weight:500}
.social{left:771px;top:26px;display:flex;gap:6px}
.social span{width:24px;height:24px;border-radius:3px;background:#5a86c9}
</style>
</head>
<body>

<header class="site-header abs">
  <div class="brand-mark abs">HBQ</div>
  <div class="brand-name abs">Harlowe<br>Print &amp; Blueprint<br>Company, Inc.</div>
  <div class="brand-tag abs">Client-Driven Service Since 1975</div>
  <div class="contact abs">
    <div>Call Today - <span class="phone">555-384-7290</span></div>
    <div>Email : <span class="mail">info@harloweprint.example</span></div>
  </div>
</header>

<section class="hero abs" role="img" aria-label="Hand holding a colour measuring device over a printed colourful calendar sheet"></section>
<ul class="main-nav abs">
  <li class="active">The HBQ Difference</li>
  <li>About</li>
  <li>Sustainability</li>
  <li>Products &amp; Services</li>
  <li>Reprographics</li>
  <li>Digital File Management</li>
  <li>Color Graphics</li>
  <li>Equipment &amp; Supplies</li>
  <li>Login</li>
  <li>Blog</li>
  <li>Contact Us</li>
</ul>
<h1 class="hero-title abs">COLOUR SERVICES FOR DESIGNER<br>&amp; MARKETERS</h1>
<div class="slider-dots abs"><span class="on"></span><span></span><span></span><span></span></div>

<div class="division-band abs"></div>
<div class="division abs" style="left:104px"><div class="disc photo" role="img" aria-label="Architectural blueprints with a pencil">Repro<br>Graphics</div></div>
<div class="division abs" style="left:296px"><div class="disc">Digital File<br>Management</div></div>
<div class="division abs" style="left:488px"><div class="disc">Color<br>Graphics</div></div>
<div class="division abs" style="left:680px"><div class="disc">Equipment<br>&amp; Supplies</div></div>

<h2 class="section-title about-title abs">About Harlowe Print</h2>
<p class="about-text abs">Harlowe Print &amp; Blueprint (HBQ) is a full service reprographics company serving Oregon and Southwest Washington's design and building community. Founded in 1975 by Daniel Korvitz, we utilize the latest digital technologies to provide a wide range of reprographics and graphic imaging services.</p>
<div class="btn about-btn abs">Read More</div>

<h2 class="section-title testi-title abs">Testimonial</h2>
<div class="arrows testi-arrows abs"><span class="prev"></span><span class="next"></span></div>
<blockquote class="testi-box">
  <span class="testi-quote-mark" aria-hidden="true">&ldquo;</span>
  <q>Aliquam molestie, mi et imperdiet euismod, dui purus auctor tellus, et interdum lacus lectus et ante. Sed accumsan sollicitudin sapien...</q>
  <cite>By &nbsp;Owen Pratley</cite>
</blockquote>

<div class="divider abs" style="top:846px"></div>

<div class="action abs" style="left:104px">
  <svg width="44" height="44" viewBox="0 0 44 44" aria-hidden="true"><rect x="6" y="18" width="24" height="20" fill="#fbf2d8" stroke="#c9a55a" transform="rotate(-12 18 28)"/><path d="M14 34 L36 8" stroke="#f0b43c" stroke-width="5" stroke-linecap="round"/><path d="M14 34 l-2 5 5-2z" fill="#333"/></svg>
  Get a Quote
</div>
<div class="action abs" style="left:360px">
  <svg width="44" height="44" viewBox="0 0 44 44" aria-hidden="true" fill="none" stroke="#fff" stroke-width="2.5" stroke-linejoin="round"><path d="M4 8h6l5 18h20l4-13H12"/><circle cx="17" cy="33" r="3"/><circle cx="32" cy="33" r="3"/></svg>
  Place Order
</div>
<div class="action plan-room abs" style="left:616px">
  <svg width="38" height="36" viewBox="0 0 48 44" aria-hidden="true"><rect x="3" y="6" width="42" height="27" rx="2" fill="#222"/><rect x="6" y="9" width="36" height="21" fill="#cfe0f2"/><rect x="20" y="33" width="8" height="5" fill="#555"/><rect x="13" y="38" width="22" height="3" fill="#777"/></svg>
  Digital Plan Room
</div>

<div class="divider abs" style="top:940px"></div>

<h2 class="section-title news-title abs">Recent News</h2>
<div class="news news-1 abs"><div class="date">07/10/13</div>3 Reasons Why Online Plan Rooms Will Make Your Project a Success</div>
<div class="news news-2 abs"><div class="date">07/10/13</div>Printing Services are Getting Social at Harlowe Print + Blueprint</div>
<div class="read-all abs">READ ALL NEWS</div>

<h2 class="section-title equip-title abs">Equipment for Sale</h2>
<div class="arrows equip-arrows abs"><span class="prev"></span><span class="next"></span></div>
<div class="equip-image abs" role="img" aria-label="Large format colour printer with paper rolls"></div>
<div class="equip-name abs">Tarvo ColorPlane 300</div>
<p class="equip-text abs">Efficient, economical large format color digital system for printing, copying, and scanning.</p>
<div class="btn equip-btn abs">Read More</div>

<footer class="site-footer abs">
  <div class="copy abs">Copyright 2013 <b>Harlowe Print &amp; Blueprint Inc.</b><br>All Right Reserved &nbsp;| &nbsp;Privacy Policy</div>
  <div class="social abs">
    <span aria-label="QN"></span><span aria-label="Chirpa" style="background:#4fb3e0"></span><span aria-label="Workrung" style="background:#3a7fc0"></span>
  </div>
</footer>

</body>
</html>
```